Freelance Translator in Need of a Business Card

I am a freelance Japanese to English translator. I work in the video game localization industry and do literary translation in my spare time. I would like to have both the English word 'Translator' and the Japanese '翻訳者' in the job title. The final design should evoke trust, openness, and reliability.

Target Market(s)

Video game localization companies
Japanese comic book artists

Industry/Entity Type

Business

Contact Information for Business Card

Daniel Forsvik, Translator
dan.forsvik@quellmail.net
torvenwords.com
social: @torven_wd

Colors

Designer to choose colors to be used in the design.

```html
<!DOCTYPE html>
<html lang="en">
<head>
<meta charset="utf-8">
<title>Torven Words — Business Card</title>
<link rel="stylesheet" href="https://fonts.googleapis.com/css2?family=Playfair+Display:wght@400;700;900&family=Noto+Serif+JP:wght@400&display=swap">
<style>
  :root {
    --backdrop: #e7e3dd;
    --card-white: #ffffff;
    --pattern-grey: #ebebeb;
    --ink: #1a1a1a;
    --ink-soft: #3a3a3a;
    --rule: #6a6a6a;
    --card-black: #141414;
    --band-white: #f4f4f4;
  }
  * { box-sizing: border-box; margin: 0; padding: 0; }
  html, body {
    width: 1200px;
    height: 892px;
    overflow: hidden;
    background: var(--backdrop);
  }
  .canvas {
    width: 1200px;
    height: 892px;
    display: flex;
    align-items: center;
    justify-content: center;
    gap: 40px;
  }
  .card {
    width: 540px;
    height: 309px;
    position: relative;
    overflow: hidden;
    box-shadow: 0 10px 28px rgba(0,0,0,0.18);
  }

  /* Front */
  .card-front { background: var(--card-white); }
  .pattern-field {
    position: absolute;
    inset: 0;
    background: var(--pattern-grey);
  }
  .info-panel {
    position: absolute;
    left: 92px; right: 92px; top: 34px; bottom: 34px;
    background: var(--card-white);
    border-radius: 22px;
    display: flex;
    flex-direction: column;
    align-items: center;
    justify-content: center;
    text-align: center;
    color: var(--ink);
    font-family: "Playfair Display", Georgia, serif;
  }
  .company-name {
    font-weight: 700;
    font-size: 27px;
    letter-spacing: 0.3px;
  }
  .divider {
    width: 90px;
    height: 1px;
    background: var(--rule);
    margin: 10px 0;
  }
  .person-name {
    font-weight: 400;
    font-size: 21px;
    color: var(--ink-soft);
    letter-spacing: 0.4px;
  }
  .job-title {
    font-size: 13px;
    margin-top: 3px;
    color: var(--ink-soft);
  }
  .job-title .ja { font-family: "Noto Serif JP", serif; }
  .contact-list {
    list-style: none;
    font-size: 14px;
    line-height: 1.45;
    color: var(--ink-soft);
  }

  /* Back */
  .card-back { background: var(--card-black); }
  .name-band {
    position: absolute;
    left: 0; right: 0;
    top: 96px;
    height: 128px;
    background: var(--band-white);
    display: flex;
    align-items: center;
    justify-content: center;
  }
  .band-title {
    font-family: "Playfair Display", Georgia, serif;
    font-weight: 700;
    font-size: 40px;
    letter-spacing: 1px;
    color: var(--ink);
  }
</style>
</head>
<body>
<main class="canvas">
  <section class="card card-front" aria-label="Card front">
    <div class="pattern-field" role="img" aria-label="Light grey geometric pattern of nested squares framing the card"></div>
    <div class="info-panel">
      <h1 class="company-name">Torven Words</h1>
      <div class="divider"></div>
      <p class="person-name">Daniel Forsvik</p>
      <p class="job-title">Translator <span class="ja">翻訳者</span></p>
      <div class="divider"></div>
      <ul class="contact-list">
        <li>dan.forsvik@quellmail.net</li>
        <li>www.torvenwords.com</li>
        <li>social: @torven_wd</li>
      </ul>
    </div>
  </section>

  <section class="card card-back" aria-label="Card back">
    <div class="name-band">
      <p class="band-title">TORVEN WORDS</p>
    </div>
  </section>
</main>
</body>
</html>
```